Business Card for a mobile physiotherapy company

I need a layout for a business card for a mobile physiotherapy company.
Slogan is "Mobile Physiotherapy - Your Road To Recovery"
Phone number is 867-555-0142
Email VardenTherapy@postnest.ca (subject to change with website)
Website www.VardenTherapy.ca
My name and credentials: Luke Varden Luke Varden, BSc(kin), MPT, CAFCI, IMS
Information maybe included: Direct Billing, Services including Physiotherapy, IMS, acupuncture
Maybe include facebook and instagram logos
One side with the logo clean and sharp
Other side with details, try not to look too busy, keep everything concise

```html
<!DOCTYPE html>
<html lang="en">
<head>
<meta charset="utf-8">
<title>Varden Therapy – Business Card</title>
<link rel="stylesheet" href="https://fonts.googleapis.com/css2?family=Tinos:wght@400;700&family=PT+Sans:wght@400;700&display=swap">
<style>
  :root {
    --backdrop: #1c1c1e;
    --forest: #0c5249;
    --forest-line: #0f5a4e;
    --navy: #2b4a74;
    --paper: #ffffff;
    --ink-light: #ffffff;
    --ink-soft: #dfe6ef;
  }
  * { margin: 0; padding: 0; box-sizing: border-box; }
  html, body { width: 1200px; height: 960px; overflow: hidden; }
  body {
    background: var(--backdrop);
    position: relative;
    font-family: "PT Sans", sans-serif;
  }
  .card {
    position: absolute;
    left: 250px;
    width: 700px;
    height: 400px;
    overflow: hidden;
    border-radius: 4px;
  }

  /* Back side */
  .card-back {
    top: 50px;
    background: var(--forest);
  }
  .card-back .social {
    position: absolute;
    top: 128px;
    left: 430px;
    display: flex;
    gap: 26px;
  }
  .card-back .social-dot {
    width: 42px;
    height: 42px;
    border-radius: 50%;
    background: var(--ink-light);
  }
  .card-back .slogan {
    position: absolute;
    top: 200px;
    left: 0;
    width: 100%;
    text-align: center;
    font-family: "Tinos", serif;
    font-weight: 700;
    font-size: 27px;
    color: var(--ink-light);
    letter-spacing: 0.5px;
  }

  /* Front side */
  .card-front {
    top: 510px;
    background: var(--paper);
  }
  .brand {
    position: absolute;
    left: 0;
    top: 0;
    width: 310px;
    height: 400px;
    display: flex;
    align-items: center;
    justify-content: center;
    gap: 12px;
  }
  .brand-mark {
    width: 20px;
    height: 20px;
    background: var(--navy);
  }
  .brand-name {
    font-family: "Tinos", serif;
    font-weight: 700;
    font-size: 38px;
    color: var(--forest);
    letter-spacing: 1px;
  }
  .divider {
    position: absolute;
    left: 300px;
    top: 0;
    width: 40px;
    height: 400px;
  }
  .details {
    position: absolute;
    left: 318px;
    top: 0;
    width: 382px;
    height: 400px;
    background: var(--navy);
    padding: 52px 0 0 52px;
    color: var(--ink-light);
  }
  .person-name {
    font-family: "Tinos", serif;
    font-weight: 700;
    font-size: 27px;
    letter-spacing: 1.5px;
    text-transform: uppercase;
  }
  .credentials {
    font-size: 15px;
    color: var(--ink-soft);
    margin-top: 2px;
  }
  .contact-list {
    list-style: none;
    margin-top: 20px;
  }
  .contact-list li {
    display: flex;
    align-items: center;
    gap: 10px;
    font-size: 20px;
    line-height: 30px;
  }
  .contact-list svg { width: 17px; height: 17px; flex: none; }
  .services-title {
    margin-top: 22px;
    font-weight: 700;
    font-size: 20px;
  }
  .services {
    display: grid;
    grid-template-columns: auto auto;
    justify-content: start;
    column-gap: 22px;
    list-style: none;
    font-size: 20px;
    line-height: 27px;
    margin-top: 2px;
  }
  .services li::before { content: "• "; }
</style>
</head>
<body>

  <section class="card card-back" aria-label="Card back">
    <div class="social" aria-label="Social media">
      <span class="social-dot"></span>
      <span class="social-dot"></span>
    </div>
    <p class="slogan">Mobile Physiotherapy - Your Road To Recovery</p>
  </section>

  <section class="card card-front" aria-label="Card front">
    <div class="brand">
      <span class="brand-mark"></span>
      <span class="brand-name">Varden Therapy</span>
    </div>

    <svg class="divider" viewBox="0 0 40 400" aria-hidden="true">
      <polyline points="30,0 30,86 20,96 30,106 30,400" fill="none" stroke="var(--forest-line)" stroke-width="5"/>
    </svg>

    <div class="details">
      <h1 class="person-name">Luke Varden</h1>
      <p class="credentials">BSc(kin), MPT, CAFCI, IMS</p>

      <ul class="contact-list">
        <li>
          <svg viewBox="0 0 20 20" aria-hidden="true"><circle cx="10" cy="10" r="8.5" fill="none" stroke="#fff" stroke-width="1.6"/><path d="M7 5.5l2 2-1 1.3a6 6 0 0 0 3.2 3.2l1.3-1 2 2-1.3 1.4c-3.5 0-7.4-3.9-7.4-7.4z" fill="#fff"/></svg>
          867-555-0142
        </li>
        <li>
          <svg viewBox="0 0 20 20" aria-hidden="true"><circle cx="10" cy="10" r="8.5" fill="none" stroke="#fff" stroke-width="1.6"/><rect x="5" y="6.5" width="10" height="7" fill="none" stroke="#fff" stroke-width="1.4"/><path d="M5 6.5l5 4 5-4" fill="none" stroke="#fff" stroke-width="1.4"/></svg>
          VardenTherapy@postnest.ca
        </li>
        <li>
          <svg viewBox="0 0 20 20" aria-hidden="true"><circle cx="10" cy="10" r="8.5" fill="none" stroke="#fff" stroke-width="1.6"/><ellipse cx="10" cy="10" rx="3.6" ry="8.5" fill="none" stroke="#fff" stroke-width="1.3"/><path d="M1.5 10h17M3 5.8h14M3 14.2h14" stroke="#fff" stroke-width="1.3"/></svg>
          www.VardenTherapy.ca
        </li>
      </ul>

      <h2 class="services-title">Services Including</h2>
      <ul class="services">
        <li>Physiotherapy</li>
        <li>Direct Billing</li>
        <li>Ims</li>
        <li>Acupuncture</li>
      </ul>
    </div>
  </section>

</body>
</html>
```